Advanced Therapeutic Massage Therapist

I need a business card advertising my massage services as an advanced therapeutic massage therapist. I offer advanced therapeutic massage, swedish and deep tissue. I want to create a simple, professional and feminine card. I like bright colours and creativity.

I prefer a bold and experimental approach rather than something status-quo. A card to suggest therapeutic healing through dynamic massage. Motifs, shapes or layout which suggest movement and flow.
Updates

Target Market(s)

Everybody!

Industry/Entity Type

Health And Wellness

Contact Information for Business Card

The card should include:
My name, logo, services offered and my contact details.

Sláine Dunleavy
Massage Therapist

- Swedish - Deep Tissue - Advanced Therapeutic

Phone: (+353) 87 216 4093
Email: regenerate@slainedunleavy-example.com
Website: www.slainedunlevy-example.com

Font styles to use
Serif
Sans Serif
Decorative
Script

Colors

Designer to choose colors to be used in the design.

Requirements
Must have
• An example may contain something like this, yet concise:
• "Sláine Dunleavy
• Massage Therapist
• - Swedish - Deep Tissue - Advanced Therapeutic"
Nice to have
• This sentence is optional:
• Imagery such as a logo or symbol. I have attached a file containing a logo I had produced however the name is incorrect now as it is "Sláine" not "Nelly". It could be edited to change it to Sláine.
• I have sent the file as .psd .jpg. .pdf and .png
• I like when the card conveys energy, movement, pressure points, flow etc.
• I just like the designer to follow their own style and ideas. I like bright colours but must have a lot of a base colour to offset it. I really prefer them to follow their own inspiration. That is my preference.
Should not have
• Pine trees, non-native trees to Britain and Ireland, exotic flowers or animals that are not native to Britain and Ireland.
• I don't like brown as the background colour of the card.
• The cars shouldn't look like a wedding invitation i.e too many floral type designs.

```html
<!DOCTYPE html>
<html lang="en">
<head>
<meta charset="utf-8">
<title>Sláine Dunleavy – Massage Therapist Business Card</title>
<link rel="stylesheet" href="https://fonts.googleapis.com/css2?family=Allura&family=Work+Sans:wght@300;400;500;600&display=swap">
<style>
  :root {
    --canvas-bg: #f3f2ef;
    --card-dark: #3a3a3c;
    --card-light: #ffffff;
    --gold: #c8923a;
    --gold-light: #e2b866;
    --teal: #a7ddcf;
    --teal-soft: #d9efe9;
    --ink: #3d3d3d;
    --muted: #8b8b8b;
    --faint-gold: #efe3cf;
  }
  * { margin: 0; padding: 0; box-sizing: border-box; }
  html, body {
    width: 1200px; height: 900px; overflow: hidden;
    background: var(--canvas-bg);
    font-family: "Work Sans", Arial, sans-serif;
  }
  .canvas { position: relative; width: 1200px; height: 900px; }

  .card {
    position: absolute;
    width: 760px; height: 400px;
    box-shadow: 0 12px 30px rgba(0,0,0,0.18);
    overflow: hidden;
  }
  .card--front {
    left: 110px; top: 50px;
    background: var(--card-dark);
    border-radius: 200px 4px 4px 200px;
  }
  .card--back {
    left: 330px; top: 470px;
    background: var(--card-light);
    border-radius: 4px 200px 200px 4px;
  }

  /* Front card */
  .emblem {
    position: absolute;
    left: 20px; top: 20px;
    width: 360px; height: 360px;
  }
  .front-text {
    position: absolute;
    left: 396px; top: 100px;
    width: 340px;
    color: var(--gold-light);
  }
  .front-text .script-name {
    font-family: "Allura", cursive;
    font-size: 50px;
    line-height: 1.1;
    color: var(--gold-light);
    white-space: nowrap;
  }
  .front-text .role {
    font-size: 19px;
    font-weight: 400;
    letter-spacing: 2px;
    color: var(--gold);
    margin: 4px 0 0 40px;
  }
  .front-text .summary {
    font-size: 12px;
    font-weight: 300;
    line-height: 1.5;
    color: var(--muted);
    margin: 22px 0 0 40px;
  }
  .front-text .services {
    font-size: 12px;
    font-weight: 300;
    color: var(--muted);
    margin: 18px 0 0 40px;
  }

  /* Back card */
  .watermark {
    position: absolute;
    right: 24px; top: 30px;
    width: 320px; height: 320px;
  }
  .back-text {
    position: absolute;
    left: 70px; top: 92px;
  }
  .back-text .name {
    font-size: 28px;
    font-weight: 600;
    color: var(--gold);
    letter-spacing: 0.5px;
  }
  .back-text .role {
    font-size: 15px;
    font-weight: 400;
    color: var(--ink);
    letter-spacing: 1px;
    margin-top: 2px;
  }
  .contact-list { list-style: none; margin-top: 16px; }
  .contact-list li {
    display: flex; align-items: center; gap: 12px;
    font-size: 18px; font-weight: 300; color: var(--ink);
    line-height: 1.4;
  }
  .contact-list svg { width: 15px; height: 15px; flex: none; }
  .service-line {
    position: absolute;
    left: 70px; bottom: 58px;
    font-size: 18px; font-weight: 300; color: var(--ink);
    letter-spacing: 0.5px;
  }
  .service-line .sep { color: var(--gold); margin: 0 7px; }
</style>
</head>
<body>
<main class="canvas">

  <section class="card card--front" aria-label="Card front">
    <svg class="emblem" viewBox="0 0 360 360">
      <defs>
        <radialGradient id="emblemFill" cx="50%" cy="45%" r="55%">
          <stop offset="0%" stop-color="#d4efe6"/>
          <stop offset="70%" stop-color="#a7ddcf"/>
          <stop offset="100%" stop-color="#8fcfbe"/>
        </radialGradient>
        <radialGradient id="wreathFill" cx="50%" cy="50%" r="50%">
          <stop offset="88%" stop-color="#3a3a3c"/>
          <stop offset="94%" stop-color="#8a6a36"/>
          <stop offset="100%" stop-color="#3a3a3c"/>
        </radialGradient>
      </defs>
      <g role="img" aria-label="Gold leafy wreath framing the emblem">
        <circle cx="180" cy="180" r="178" fill="url(#wreathFill)"/>
      </g>
      <circle cx="180" cy="180" r="150" fill="none" stroke="#c8923a" stroke-width="5"/>
      <g role="img" aria-label="Gold filigree tree of life on a mint circle">
        <circle cx="180" cy="180" r="147" fill="url(#emblemFill)"/>
      </g>
    </svg>

    <div class="front-text">
      <div class="script-name">Sláine Dunleavy</div>
      <div class="role">massage therapist</div>
      <p class="summary">CTHB qualified specialising in advanced<br>therapeutic and deep tissue massage.</p>
      <p class="services">Swedish | Deep Tissue | Advanced Therapeutic</p>
    </div>
  </section>

  <section class="card card--back" aria-label="Card back">
    <svg class="watermark" viewBox="0 0 360 360" role="img" aria-label="Faint gold tree of life emblem">
      <defs>
        <radialGradient id="watermarkFill" cx="50%" cy="50%" r="50%">
          <stop offset="0%" stop-color="#f6efe4"/>
          <stop offset="100%" stop-color="#efe3cf"/>
        </radialGradient>
      </defs>
      <circle cx="180" cy="180" r="172" fill="url(#watermarkFill)" opacity="0.7"/>
    </svg>

    <div class="back-text">
      <h1 class="name">SLÁINE DUNLEAVY</h1>
      <p class="role">MASSAGE THERAPIST</p>
      <ul class="contact-list">
        <li>
          <svg viewBox="0 0 24 24" aria-hidden="true"><path d="M6.6 10.8c1.4 2.8 3.8 5.1 6.6 6.6l2.2-2.2c.3-.3.7-.4 1-.2 1.1.4 2.3.6 3.6.6.6 0 1 .4 1 1V20c0 .6-.4 1-1 1C10.6 21 3 13.4 3 4c0-.6.4-1 1-1h3.5c.6 0 1 .4 1 1 0 1.3.2 2.5.6 3.6.1.3 0 .7-.2 1z" fill="var(--gold)"/></svg>
          (+353) 87 216 4093
        </li>
        <li>
          <svg viewBox="0 0 24 24" aria-hidden="true"><rect x="2.5" y="5" width="19" height="14" rx="1.5" fill="none" stroke="var(--gold)" stroke-width="2"/><path d="M3 6l9 7 9-7" fill="none" stroke="var(--gold)" stroke-width="2"/></svg>
          slainemassage@example-mail.com
        </li>
      </ul>
    </div>

    <p class="service-line">Swedish<span class="sep">|</span>Deep<span class="sep">|</span>Tissue<span class="sep">|</span>Advanced<span class="sep">|</span>Therapeutic</p>
  </section>

</main>
</body>
</html>
```